Quiet Lanterns for the Restless Inner Mind

I would like a website designed that would be used to upload podcasts, videos and written material about mental health. Where people will be being as honest, open and truthful as they can about mental health issues.
I would like it to look calming and soothing. Inspired by Dorlac's paintings and colour schemes.

I am on Brightlane as Dr Helen Maddox - and chirpbox as drhelenmaddox

Target Market(s)

Healthcare professionals and users of services who want to think at a deeper level about the nature of mental illness

Number of Pages Required

1 page

```html
<!DOCTYPE html>
<html lang="en">
<head>
<meta charset="utf-8">
<title>Dr Helen Maddox — Mental Health</title>
<link href="https://fonts.googleapis.com/css2?family=Lexend:wght@400;500;600&family=Poppins:wght@300;400;500;600&display=swap" rel="stylesheet">
<style>
:root{
  --yellow:#fde61f;
  --ink:#111111;
  --text:#3a3a3a;
  --cream:#fdfbec;
  --white:#ffffff;
  --red:#e0303a;
  --footer:#000000;
}
*{box-sizing:border-box;margin:0;padding:0}
html,body{width:1200px;height:4392px;overflow:hidden;background:var(--white)}
body{font-family:"Poppins",sans-serif;color:var(--ink)}
.page{position:relative;width:1200px;height:4392px;overflow:hidden}
.abs{position:absolute}
.label{font-family:"Poppins",sans-serif;font-weight:300;font-size:20px;letter-spacing:.3px;color:var(--ink);text-transform:uppercase;white-space:nowrap}
.heading{font-family:"Lexend",sans-serif;font-weight:500;font-size:40px;line-height:51px;color:var(--ink)}
.para{font-family:"Poppins",sans-serif;font-weight:300;font-size:15.5px;line-height:30px;color:var(--text);text-align:justify}
.btn{display:flex;align-items:center;justify-content:center;border-radius:26px;font-family:"Poppins",sans-serif;font-weight:400;font-size:17px;text-transform:uppercase;color:var(--ink);background:var(--yellow)}
.btn--dark{background:var(--ink);color:var(--white)}
.photo{position:absolute}

.topbar{left:0;top:0;width:1200px;height:70px;background:rgba(40,40,40,.75)}
.brand{display:flex;align-items:center;gap:8px}
.brand__dot{width:52px;height:52px;border-radius:50%;border:3px solid var(--yellow)}
.brand__name{font-family:"Lexend",sans-serif;font-weight:500;font-size:25px;color:var(--white);line-height:28px;white-space:nowrap}
.brand__tag{font-family:"Poppins",sans-serif;font-size:13px;letter-spacing:6px;color:#ddd;line-height:16px;white-space:nowrap}
.nav{font-family:"Poppins",sans-serif;font-weight:500;font-size:16px;color:var(--white);top:20px}
.contact-btn{left:914px;top:12px;width:156px;height:46px;background:var(--white);border-radius:24px;font-size:16px;font-weight:500}

.hero-photo{left:0;top:0;width:1200px;height:700px;background:linear-gradient(100deg,#ede67c 0%,#e6dc6b 35%,#c9bda0 55%,#8c8a8e 75%,#5c5f6a 100%)}
.hero-title{font-family:"Lexend",sans-serif;font-weight:500;font-size:48px;line-height:52px;color:var(--ink);white-space:nowrap}

.card{position:absolute;background:var(--white);box-shadow:0 3px 10px rgba(0,0,0,.08)}
.card__title{font-family:"Lexend",sans-serif;font-weight:500;font-size:17px;color:var(--ink);white-space:nowrap}
.kebab{position:absolute;width:4px;height:22px;background:radial-gradient(circle,#bbb 2px,transparent 2.5px) 0 0/4px 8px repeat-y}

.tcard{position:absolute;width:262px;height:339px;text-align:center}
.tcard__avatar{position:absolute;left:103px;top:26px;width:56px;height:56px;border-radius:50%}
.tcard__name{position:absolute;left:0;top:106px;width:100%;font-family:"Poppins",sans-serif;font-weight:600;font-size:15.5px;color:var(--ink)}
.tcard__text{position:absolute;left:28px;top:141px;width:206px;font-family:"Poppins",sans-serif;font-weight:300;font-size:15px;line-height:26px;color:var(--ink);text-align:justify;text-align-last:center;hyphens:auto}

.footer-nav{font-family:"Poppins",sans-serif;font-weight:500;font-size:15px;color:var(--white);top:4180px}
</style>
</head>
<body>
<div class="page">

  <!-- HERO -->
  <div class="photo hero-photo" role="img" aria-label="Counselling session: a woman seated on a sofa listening to a therapist, washed in soft yellow"></div>
  <svg class="abs" style="left:0;top:0" width="1200" height="700" viewBox="0 0 1200 700">
    <path d="M0,588 C180,640 340,600 520,585 C720,568 900,660 1200,640 L1200,700 L0,700Z" fill="#fde61f"/>
    <path d="M0,588 C160,630 320,610 480,590 C660,570 820,650 1200,618 L1200,700 L0,700Z" fill="#ffffff"/>
    <path d="M480,620 C700,640 900,700 1200,690 L1200,700 L480,700Z" fill="#ffffff"/>
  </svg>
  <div class="abs topbar"></div>
  <div class="abs brand" style="left:88px;top:8px">
    <div class="brand__dot"></div>
    <div>
      <div class="brand__name">Dr. Helen Maddox</div>
      <div class="brand__tag">MENTAL HEALTH</div>
    </div>
  </div>
  <div class="abs nav" style="left:467px">HOME</div>
  <div class="abs nav" style="left:566px">ABOUT US</div>
  <div class="abs nav" style="left:697px">SERVICE</div>
  <div class="abs nav" style="left:813px">PAGES</div>
  <div class="abs btn contact-btn">CONTACT US</div>

  <div class="abs label" style="left:112px;top:210px">Welcome to Dr Helen Maddox</div>
  <div class="abs hero-title" style="left:107px;top:250px">Get care from the<br>people who care.</div>
  <div class="abs btn" style="left:109px;top:389px;width:181px;height:47px;font-size:16px">GET STARTED</div>

  <!-- ABOUT MENTAL HEALTH -->
  <div class="photo" style="left:111px;top:716px;width:429px;height:453px;background:linear-gradient(135deg,#e3e4e8,#b9b9be 50%,#d8c9bb)" role="img" aria-label="A therapist in conversation with an older client in a bright room"></div>
  <div class="abs" style="left:361px;top:983px;width:179px;height:186px;background:var(--white)"></div>
  <div class="abs" style="left:370px;top:1010px;font-family:'Lexend',sans-serif;font-weight:600;font-size:88px;line-height:90px">15+</div>
  <div class="abs" style="left:371px;top:1107px;font-family:'Poppins',sans-serif;font-weight:600;font-size:15.5px;white-space:nowrap">YEARS EXPERIENCE</div>

  <div class="abs label" style="left:593px;top:738px">About Mental Health</div>
  <div class="abs heading" style="left:593px;top:772px;white-space:nowrap">No more feeling<br>Uncomfortable.</div>
  <p class="abs para" style="left:593px;top:894px;width:485px">Sed ut perspiciatis unde omnis iste natus error sit voluptatem accusantium doloremque laudantium, totam rem aperiam, eaque ipsa quae ab illo inventore veritatis et quasi architecto beatae vitae dicta sunt explicabo. Nemo enim ipsam voluptatem quia voluptas sit aspernatur aut odit aut fugit, sed quia dolor sit amet, consectetur</p>
  <div class="abs btn" style="left:598px;top:1116px;width:183px;height:50px">READ MORE</div>

  <!-- VIDEO -->
  <div class="photo" style="left:0;top:1290px;width:112px;height:546px;background:linear-gradient(180deg,#b5a8bd,#d9d6e3 50%,#7e86a8)" role="img" aria-label="Softly lit room interior"></div>
  <div class="abs" style="left:112px;top:1290px;width:333px;height:546px;background:var(--yellow)"></div>
  <div class="photo" style="left:445px;top:1290px;width:755px;height:546px;background:linear-gradient(110deg,#a99a9c 0%,#7e7c8a 35%,#5c6278 60%,#6f6a6a 80%,#4e5a44 100%)" role="img" aria-label="Video still: two women talking in a counselling session"></div>
  <svg class="abs" style="left:759px;top:1523px" width="80" height="80" viewBox="0 0 80 80">
    <circle cx="40" cy="40" r="40" fill="#e0303a"/>
    <path d="M31,25 L56,40 L31,55Z" fill="#ffffff"/>
  </svg>
  <div class="abs label" style="left:154px;top:1408px">Video</div>
  <div class="abs heading" style="left:154px;top:1455px;width:280px">Discover The Faces Behind Our Mental Health Consultancy</div>

  <!-- PODCAST -->
  <div class="abs" style="left:0;top:1836px;width:1200px;height:559px;background:var(--cream)"></div>
  <div class="abs label" style="left:157px;top:1922px">Podcast</div>

  <div class="card" style="left:153px;top:1999px;width:273px;height:271px">
    <div class="photo" style="left:0;top:0;width:273px;height:207px;background:linear-gradient(135deg,#8a8580,#c8a796 60%,#e26f3a)" role="img" aria-label="Two hands held together in comfort"></div>
    <div class="abs card__title" style="left:20px;top:228px">Lorem ipsum dolor</div>
    <div class="kebab" style="left:244px;top:228px"></div>
  </div>
  <div class="card" style="left:445px;top:1974px;width:324px;height:322px;background:var(--yellow)">
    <div class="photo" style="left:0;top:0;width:324px;height:196px;background:linear-gradient(135deg,#c9cdd3,#9aa1a9 50%,#5c4a3f)" role="img" aria-label="Smiling podcast guest in a bright office"></div>
    <div class="abs card__title" style="left:24px;top:210px;font-size:19px">Lorem ipsum dolor</div>
    <svg class="abs" style="left:24px;top:245px" width="80" height="16" viewBox="0 0 80 16">
      <g fill="#c9b43a">
        <path d="M8,1 L10,6 L15,6 L11,9.5 L12.5,15 L8,11.8 L3.5,15 L5,9.5 L1,6 L6,6Z"/>
        <path transform="translate(15 0)" d="M8,1 L10,6 L15,6 L11,9.5 L12.5,15 L8,11.8 L3.5,15 L5,9.5 L1,6 L6,6Z"/>
        <path transform="translate(30 0)" d="M8,1 L10,6 L15,6 L11,9.5 L12.5,15 L8,11.8 L3.5,15 L5,9.5 L1,6 L6,6Z"/>
        <path transform="translate(45 0)" d="M8,1 L10,6 L15,6 L11,9.5 L12.5,15 L8,11.8 L3.5,15 L5,9.5 L1,6 L6,6Z"/>
        <path transform="translate(60 0)" d="M8,1 L10,6 L15,6 L11,9.5 L12.5,15 L8,11.8 L3.5,15 L5,9.5 L1,6 L6,6Z"/>
      </g>
    </svg>
    <div class="abs" style="left:108px;top:245px;font-size:12px">(10)</div>
    <svg class="abs" style="left:24px;top:276px" width="22" height="14" viewBox="0 0 22 14">
      <path d="M1,7 C5,1 17,1 21,7 C17,13 5,13 1,7Z" fill="none" stroke="#111" stroke-width="1.6"/>
      <circle cx="11" cy="7" r="3" fill="#111"/>
    </svg>
    <div class="abs" style="left:55px;top:275px;font-size:12px">1,457</div>
    <svg class="abs" style="left:214px;top:272px" width="20" height="22" viewBox="0 0 20 22">
      <path d="M7,20 L4,13 C3.5,11.5 5,10.8 6,12 L7,13.5 L7,3 C7,1.5 9,1.5 9,3 L9,9 L9,8 C9,6.5 11,6.5 11,8 L11,9.5 C11,8 13,8 13,9.5 L13,10.5 C13,9 15,9 15,10.5 L15,16 L13,20Z" fill="none" stroke="#111" stroke-width="1.3"/>
    </svg>
    <div class="kebab" style="left:290px;top:276px"></div>
  </div>
  <div class="card" style="left:786px;top:1999px;width:273px;height:271px">
    <div class="photo" style="left:0;top:0;width:273px;height:207px;background:linear-gradient(135deg,#6d5a5e,#a88d86 50%,#3f3a43)" role="img" aria-label="Young people in a group support session"></div>
    <div class="abs card__title" style="left:20px;top:228px">Lorem ipsum dolor</div>
    <div class="kebab" style="left:244px;top:228px"></div>
  </div>
  <svg class="abs" style="left:580px;top:2347px" width="34" height="18" viewBox="0 0 34 18">
    <path d="M7,4 L2,9 L7,14" fill="none" stroke="#111" stroke-width="2.5"/>
    <circle cx="17" cy="9" r="3.5" fill="#111"/>
    <path d="M27,4 L32,9 L27,14" fill="none" stroke="#111" stroke-width="2.5"/>
  </svg>

  <!-- ABOUT ME -->
  <div class="abs" style="left:0;top:2600px;width:360px;height:362px;background:radial-gradient(ellipse at 20% 70%,rgba(200,190,235,.45),rgba(255,255,255,0) 65%)" role="img" aria-label="Faint watercolour wash in lavender"></div>
  <div class="abs label" style="left:112px;top:2539px">About Me</div>
  <div class="abs heading" style="left:112px;top:2576px;white-space:nowrap">Dr Helen Maddox</div>
  <p class="abs para" style="left:112px;top:2648px;width:560px;font-size:15px;text-align:left">Consultant Psychiatrist, RCMindcare: Chair Working Group on the Effect of Suicide and Homicide on Clinicians, Co-Chair Patient Safety Group, Vice Chair Psychotherapy Faculty, Psychoanalyst, Group Analyst</p>
  <div class="abs btn" style="left:109px;top:2777px;width:182px;height:48px">READ MORE</div>
  <div class="abs" style="left:752px;top:2555px;width:335px;height:333px;background:var(--yellow)"></div>
  <div class="photo" style="left:752px;top:2502px;width:335px;height:386px;background:linear-gradient(160deg,rgba(190,140,120,.55) 0%,rgba(230,180,160,.55) 100%)" role="img" aria-label="Portrait photograph of Dr Helen Maddox"></div>

  <!-- MATERIAL -->
  <div class="abs" style="left:0;top:2962px;width:1200px;height:633px;background:var(--yellow)"></div>
  <div class="photo" style="left:0;top:2962px;width:760px;height:633px;background:linear-gradient(90deg,#6f5a3d 0%,#b89a5e 30%,#e8d46a 65%,rgba(253,230,31,0) 100%)" role="img" aria-label="Two young women sharing a comforting moment"></div>
  <div class="abs label" style="left:612px;top:3067px">Material About Mental Health</div>
  <div class="abs heading" style="left:608px;top:3104px;white-space:nowrap">Empowering Minds<br>Our Mental Health</div>
  <p class="abs para" style="left:607px;top:3225px;width:484px">Sed ut perspiciatis unde omnis iste natus error sit voluptatem accusantium doloremque laudantium, totam rem aperiam, eaque ipsa quae ab illo inventore veritatis et quasi architecto beatae vitae dicta sunt explicabo. Nemo enim ipsam voluptatem quia voluptas sit aspernatur aut odit aut fugit, sed quia dolor sit amet, consectetur</p>
  <div class="abs btn btn--dark" style="left:612px;top:3448px;width:182px;height:50px">READ MORE</div>

  <!-- TESTIMONIALS -->
  <div class="abs" style="left:0;top:3595px;width:1200px;height:530px;background:linear-gradient(135deg,#f7f7f7,#ececec 50%,#f8f8f8)"></div>
  <div class="abs label" style="left:112px;top:3720px">Testimonials</div>
  <div class="abs heading" style="left:113px;top:3775px;white-space:nowrap;line-height:54px">Healing Words<br>Testimonials From A<br>Mental Health<br>Consultant</div>

  <div class="tcard" style="left:541px;top:3694px;background:var(--yellow)">
    <div class="tcard__avatar" style="background:linear-gradient(180deg,#5a6580,#2e3850)" role="img" aria-label="Client portrait"></div>
    <div class="tcard__name">LOREM IPSUM DOLOR</div>
    <div class="tcard__text">Lorem ipsum dolor sit amet, consectetur adipiscing elit, sed do eiusmod tempor incididunt ut labore et dolore magna aliqua.</div>
    <svg class="abs" style="left:202px;top:303px" width="18" height="20" viewBox="0 0 20 22">
      <path d="M7,20 L4,13 C3.5,11.5 5,10.8 6,12 L7,13.5 L7,3 C7,1.5 9,1.5 9,3 L9,9 L9,8 C9,6.5 11,6.5 11,8 L11,9.5 C11,8 13,8 13,9.5 L13,10.5 C13,9 15,9 15,10.5 L15,16 L13,20Z" fill="none" stroke="#111" stroke-width="1.3"/>
    </svg>
  </div>
  <div class="tcard" style="left:825px;top:3694px;background:var(--white);border:1.5px solid #333">
    <div class="tcard__avatar" style="left:102px;top:25px;background:linear-gradient(180deg,#c9c9c9,#8e8e8e)" role="img" aria-label="Client portrait"></div>
    <div class="tcard__name" style="top:105px">LOREM IPSUM DOLOR</div>
    <div class="tcard__text" style="left:27px;top:140px">Lorem ipsum dolor sit amet, consectetur adipiscing elit, sed do eiusmod tempor incididunt ut labore et dolore magna aliqua.</div>
  </div>
  <svg class="abs" style="left:1056px;top:4053px" width="34" height="18" viewBox="0 0 34 18">
    <path d="M7,4 L2,9 L7,14" fill="none" stroke="#111" stroke-width="2.5"/>
    <circle cx="17" cy="9" r="3.5" fill="#111"/>
    <path d="M27,4 L32,9 L27,14" fill="none" stroke="#111" stroke-width="2.5"/>
  </svg>

  <!-- FOOTER -->
  <div class="abs" style="left:0;top:4125px;width:1200px;height:267px;background:var(--footer)"></div>
  <div class="abs brand" style="left:109px;top:4178px">
    <div class="brand__dot" style="width:56px;height:56px"></div>
    <div>
      <div class="brand__name">Dr. Helen Maddox</div>
      <div class="brand__tag" style="letter-spacing:8px">MENTAL HEALTH</div>
    </div>
  </div>
  <div class="abs footer-nav" style="left:470px">HOME</div>
  <div class="abs footer-nav" style="left:569px">ABOUT US</div>
  <div class="abs footer-nav" style="left:701px">SERVICE</div>
  <div class="abs footer-nav" style="left:816px">TESTIMONIALS</div>
  <div class="abs footer-nav" style="left:978px">CONTACT US</div>
  <div class="abs" style="left:470px;top:4218px;width:617px;height:1px;background:#bbb"></div>
  <div class="abs" style="left:866px;top:4232px;font-size:12.5px;color:#fff">TERM OF USE</div>
  <div class="abs" style="left:977px;top:4232px;font-size:12.5px;color:#fff">PRIVACY POLICY</div>
  <div class="abs" style="left:118px;top:4352px;font-size:14px;color:#fff">© 2023 Dr Helen Maddox</div>
  <div class="abs" style="left:520px;top:4352px;font-size:14px;color:#fff">chirpbox&nbsp;&nbsp;·&nbsp;&nbsp;Brightlane</div>

</div>
</body>
</html>
```